Bayward Vale Physiotherapy Website www.baywardvalephysiotherapy.com.au

Create Wordpress website for Bayward Vale Physiotherapy which aligns with our other locations www.oakmerephysiotherapy,com.au. We would like the website to present in a similar fashion to our exisiting site with similar headings and layout. We will then alter the text to make it location specific.

Coding

Coded - Design and coding required

Number of Pages Required

1 page

Font styles to use
Sans Serif

Requirements
Must have
• Colours of the website must match the colours of the colour Bayward Vale Physiotherapy logo
• Website must be complimentary to existing websites,
• www.oakmerephysiotherapy.com.au
• www.oakmerepilatesandrehab.com.au

```html
<!DOCTYPE html>
<html lang="en">
<head>
<meta charset="utf-8">
<title>Bayward Vale Physiotherapy</title>
<link href="https://fonts.googleapis.com/css2?family=Lato:wght@400;700;900&display=swap" rel="stylesheet">
<style>
:root{
  --navy:#1f2a5c;
  --sage:#7db39e;
  --mauve:#b7adae;
  --blue:#3b8fd8;
  --grey-bg:#f1f1f1;
  --card:#f8f8f8;
  --text:#555;
  --dark:#3b3b3b;
  --darker:#2b2b2b;
}
*{margin:0;padding:0;box-sizing:border-box}
html,body{width:1200px;height:4306px;overflow:hidden}
body{font-family:'Lato',sans-serif;color:var(--text);background:#fff}
.container{width:1050px;margin:0 auto}
.section-title{font-size:30px;font-weight:900;color:var(--navy);text-align:center;letter-spacing:.5px;text-transform:uppercase}
.title-rule{display:block;width:150px;height:3px;background:var(--navy);margin:14px auto 0;border-radius:2px}
.btn{display:inline-block;height:44px;line-height:44px;padding:0 26px;font-size:13px;font-weight:700;color:#fff;text-transform:uppercase;letter-spacing:.5px}
.btn-sage{background:var(--sage)}
.btn-mauve{background:var(--mauve)}

/* header */
.site-header{height:115px;display:flex;align-items:center;justify-content:space-between;padding:0 68px 0 76px}
.brand{display:flex;align-items:center;gap:12px;font-size:22px;font-weight:900;color:var(--navy)}
.brand-dot{width:22px;height:22px;border-radius:50%;background:var(--navy)}
.main-nav{display:flex;gap:4px}
.main-nav a{font-size:13px;font-weight:700;color:var(--navy);text-transform:uppercase;padding:10px 12px;text-decoration:none}
.main-nav a.active{background:var(--sage);color:#fff}

/* hero */
.hero{height:551px;position:relative;background:linear-gradient(160deg,#f6f7f8 0%,#e3e6ea 28%,#b9c3cf 52%,#8797a8 70%,#4d5560 100%)}
.slider-dots{position:absolute;bottom:22px;left:50%;transform:translateX(-50%);display:flex;gap:12px}
.slider-dots span{width:10px;height:10px;border-radius:50%;background:#fff;opacity:.6}
.slider-dots span:first-child{opacity:1}

/* welcome */
.welcome{height:419px;padding-top:44px;text-align:center}
.welcome-text{width:1050px;margin:30px auto 0;font-size:14px;line-height:24px}
.welcome-text p+p{margin-top:14px}
.welcome-actions{margin-top:30px;display:flex;justify-content:center;gap:26px}
.welcome-actions .btn{width:180px;padding:0}

/* services */
.services{height:860px;background:var(--grey-bg);padding-top:44px}
.service-grid{display:grid;grid-template-columns:repeat(3,330px);justify-content:space-between;row-gap:34px;margin-top:40px}
.service-card{height:267px;background:var(--card);text-align:center;padding:26px 30px 0}
.service-card.featured{background:#fff;box-shadow:0 4px 14px rgba(0,0,0,.18)}
.service-icon{width:64px;height:64px;margin:0 auto 12px;display:block}
.service-card h3{font-size:20px;font-weight:700;color:var(--navy);margin-bottom:8px}
.service-card p{font-size:14px;line-height:20px}
.services-action{text-align:center;margin-top:38px}

/* tiles */
.feature-tiles{height:553px;padding-top:45px}
.tile-grid{display:grid;grid-template-columns:513px 513px;justify-content:space-between;row-gap:32px}
.tile{height:212px;position:relative;display:flex;align-items:center;justify-content:center}
.tile-photo{position:absolute;inset:0;background:linear-gradient(135deg,#7b7f9e,#4c507c)}
.tile span{position:relative;color:#fff;font-size:30px;font-weight:900;text-transform:uppercase;letter-spacing:.5px}

/* practitioners */
.practitioners{height:646px;background:var(--grey-bg);padding-top:52px}
.practitioners-intro{width:1050px;margin:28px auto 0;text-align:center;font-size:14px;line-height:22px}
.team-grid{width:1080px;margin:38px auto 0;display:grid;grid-template-columns:repeat(4,270px)}
.member{text-align:center}
.portrait{width:180px;height:180px;border-radius:50%;margin:0 auto;border:4px solid var(--sage);background:linear-gradient(180deg,#d3d3d3,#9a9a9a)}
.member h4{margin-top:26px;font-size:15px;font-weight:900;color:#222;text-transform:uppercase}
.member .role{font-size:13px;font-weight:700;color:#333;margin-top:2px}
.member .creds{font-size:13px;line-height:18px;margin-top:4px;padding:0 30px}
.more-icon{display:block;margin:12px auto 0}

/* blog */
.blog{height:689px;padding-top:62px}
.post-grid{display:grid;grid-template-columns:repeat(3,325px);justify-content:space-between;margin-top:36px}
.post-image{height:238px}
.post h3{font-size:16px;font-weight:900;color:var(--navy);line-height:20px;margin-top:18px}
.post .date{font-size:13px;font-weight:700;color:#444;margin-top:2px}
.post p{font-size:13px;line-height:18px;margin-top:4px}
.post .read-more{font-size:13px;color:var(--sage);display:block;margin-top:12px}
.blog-action{text-align:center;margin-top:34px}

/* locations */
.locations{height:301px;background:var(--dark);padding-top:46px;color:#e4e4e4}
.locations .section-title{color:#fff}
.location-grid{display:grid;grid-template-columns:repeat(3,330px);justify-content:space-between;margin-top:34px}
.location h5{font-size:13px;font-weight:900;color:var(--sage);text-transform:uppercase;margin-bottom:6px}
.location p{font-size:13px;line-height:18px}
.contact-line{display:flex;align-items:center;gap:10px;font-size:13px;margin-top:8px}
.contact-line svg{flex:none}

/* footer */
.site-footer{height:172px;background:var(--darker);text-align:center;padding-top:50px}
.footer-nav{display:flex;justify-content:center;gap:26px}
.footer-nav a{font-size:13px;font-weight:700;color:#fff;text-transform:uppercase;text-decoration:none}
.copyright{font-size:12px;color:#aaa;margin-top:14px}
.social{display:flex;justify-content:center;gap:16px;margin-top:20px}
.social span{width:18px;height:18px;border-radius:50%;background:#ddd}
</style>
</head>
<body>

<header class="site-header">
  <div class="brand"><span class="brand-dot"></span>Bayward Vale Physiotherapy</div>
  <nav class="main-nav">
    <a class="active">Home</a><a>About</a><a>Services</a><a>Conditions</a><a>Health Tips</a><a>Blog</a><a>Careers</a><a>Contact</a>
  </nav>
</header>

<section class="hero" role="img" aria-label="Patient exercising on a pilates reformer in the clinic studio">
  <div class="slider-dots"><span></span><span></span><span></span><span></span></div>
</section>

<section class="welcome">
  <h1 class="section-title">Welcome to Bayward Vale Physiotherapy</h1>
  <span class="title-rule"></span>
  <div class="welcome-text">
    <p>Bayward Vale Physiotherapy is an innovative physiotherapy practice offering comprehensive services by experienced and highly-qualified physiotherapists. We achieve outstanding clinical results for a broad range of common conditions including: back pain, neck pain, headache, migraine, shoulder pain, sports injuries, vertigo, knee pain, incontinence, persistent pelvic pain and women's health and men's health issues.</p>
    <p>Our team of physiotherapists have extensive experience from working in private practice, private and public hospitals, and research and teaching over a range of physiotherapy disciplines including sports, manipulative, musculoskeletal, neurological, pain management, continence, women's / men's health and paediatric services.</p>
  </div>
  <div class="welcome-actions">
    <a class="btn btn-sage">Book Online Here</a>
    <a class="btn btn-mauve">Read More</a>
  </div>
</section>

<section class="services">
  <h2 class="section-title">Our Services</h2>
  <span class="title-rule"></span>
  <div class="container service-grid">
    <article class="service-card featured">
      <svg class="service-icon" viewBox="0 0 64 64" role="img" aria-label="Medical cross icon"><path d="M24 8h16v16h16v16H40v16H24V40H8V24h16z" fill="var(--blue)"/></svg>
      <h3>Physiotherapy</h3>
      <p>Our team of experienced physiotherapists have a wide range of specialities and are well placed to diagnose and manage your problem.</p>
    </article>
    <article class="service-card">
      <svg class="service-icon" viewBox="0 0 64 64" role="img" aria-label="Spine icon"><g fill="var(--blue)"><rect x="22" y="4" width="20" height="8" rx="3"/><rect x="21" y="14" width="22" height="8" rx="3"/><rect x="20" y="24" width="24" height="8" rx="3"/><rect x="20" y="34" width="24" height="8" rx="3"/><rect x="21" y="44" width="22" height="8" rx="3"/><rect x="23" y="54" width="18" height="7" rx="3"/></g></svg>
      <h3>Chronic Pain Management</h3>
      <p>We all understand the complex nature of chronic pain and the need for a multidisciplinary, Biopsychosocial approach.</p>
    </article>
    <article class="service-card">
      <svg class="service-icon" viewBox="0 0 64 64" role="img" aria-label="Knee joint icon"><path d="M18 6l12 26-4 26" fill="none" stroke="var(--blue)" stroke-width="8" stroke-linecap="round" stroke-linejoin="round"/><circle cx="30" cy="32" r="8" fill="var(--blue)"/><path d="M44 22l8-4M46 32h9M44 42l8 4" stroke="var(--blue)" stroke-width="3" stroke-linecap="round"/></svg>
      <h3>Knee Clinic</h3>
      <p>The knee pain clinic provides a complete approach for those suffering from knee pain, recovering from knee surgery or knee injury.</p>
    </article>
    <article class="service-card">
      <svg class="service-icon" viewBox="0 0 64 64" role="img" aria-label="Ultrasound monitor icon"><rect x="8" y="12" width="48" height="32" rx="3" fill="none" stroke="var(--blue)" stroke-width="4"/><path d="M14 30h8l4-8 6 14 4-6h14" fill="none" stroke="var(--blue)" stroke-width="3" stroke-linejoin="round"/><rect x="26" y="46" width="12" height="6" fill="var(--blue)"/><rect x="20" y="52" width="24" height="4" rx="2" fill="var(--blue)"/></svg>
      <h3>Real Time Ultrasound</h3>
      <p>Physiotherapists use real time ultrasound to examine how the small stabilising muscles of the spine are functioning.</p>
    </article>
    <article class="service-card">
      <svg class="service-icon" viewBox="0 0 64 64" role="img" aria-label="Female and male symbols icon"><g fill="none" stroke="var(--blue)" stroke-width="4" stroke-linecap="round"><circle cx="18" cy="24" r="11"/><path d="M18 35v20M11 47h14"/><circle cx="42" cy="36" r="11"/><path d="M50 28l9-9M51 19h8v8"/></g></svg>
      <h3>Women's &amp; Men's Health</h3>
      <p>Our specialised Women's and Men's Health clinic is dedicated to addressing the often-distressing symptoms of incontinence, pelvic pain, and bladder and bowel dysfunction.</p>
    </article>
    <article class="service-card">
      <svg class="service-icon" viewBox="0 0 64 64" role="img" aria-label="Add more icon"><circle cx="32" cy="30" r="22" fill="var(--blue)"/><path d="M32 18v24M20 30h24" stroke="#fff" stroke-width="6" stroke-linecap="round"/></svg>
      <h3>Other Services</h3>
      <p>We have a range of other services available at Bayward Vale Physiotherapy. Click here for more information</p>
    </article>
  </div>
  <div class="services-action"><a class="btn btn-sage">View All Services</a></div>
</section>

<section class="feature-tiles">
  <div class="container tile-grid">
    <a class="tile"><div class="tile-photo" role="img" aria-label="Physiotherapist treating a patient's shoulder"></div><span>Services</span></a>
    <a class="tile"><div class="tile-photo" role="img" aria-label="Practitioner guiding a patient through exercise"></div><span>About Us</span></a>
    <a class="tile"><div class="tile-photo" role="img" aria-label="Clinic reception and entrance"></div><span>Our Location</span></a>
    <a class="tile"><div class="tile-photo" role="img" aria-label="Appointment calendar on a laptop"></div><span>Book an Appointment</span></a>
  </div>
</section>

<section class="practitioners">
  <h2 class="section-title">Our Practitioners</h2>
  <span class="title-rule"></span>
  <p class="practitioners-intro">All practitioners at our clinic have completed or are completing postgraduate university training and most are involved in teaching, university lecturing and research. This means that you are being treated by highly qualified people at the forefront of new developments in the management of musculoskeletal disorders.</p>
  <div class="team-grid">
    <div class="member">
      <div class="portrait" role="img" aria-label="Portrait of Clara Whitfield"></div>
      <h4>Clara Whitfield</h4><div class="role">Director</div>
      <p class="creds">B Physio Post Grad Cert Physio (Continence &amp; Women's Health)</p>
      <svg class="more-icon" width="18" height="18" viewBox="0 0 18 18"><circle cx="9" cy="9" r="9" fill="var(--sage)"/><path d="M9 5v8M5 9h8" stroke="#fff" stroke-width="2"/></svg>
    </div>
    <div class="member">
      <div class="portrait" role="img" aria-label="Portrait of Dr Miriam Ashby"></div>
      <h4>Dr Miriam Ashby</h4><div class="role">Director</div>
      <p class="creds">B App Sc (Physio) Grad Dip (Manip Physio) PhD (Director)</p>
      <svg class="more-icon" width="18" height="18" viewBox="0 0 18 18"><circle cx="9" cy="9" r="9" fill="var(--sage)"/><path d="M9 5v8M5 9h8" stroke="#fff" stroke-width="2"/></svg>
    </div>
    <div class="member">
      <div class="portrait" role="img" aria-label="Portrait of Rebecca Thornley"></div>
      <h4>Rebecca Thornley</h4><div class="role">Director</div>
      <p class="creds">B App Sci (Physio) Post Grad Cert Physio (Continence &amp; Women's Health)</p>
      <svg class="more-icon" width="18" height="18" viewBox="0 0 18 18"><circle cx="9" cy="9" r="9" fill="var(--sage)"/><path d="M9 5v8M5 9h8" stroke="#fff" stroke-width="2"/></svg>
    </div>
    <div class="member">
      <div class="portrait" role="img" aria-label="Portrait of Daniel Kessler"></div>
      <h4>Daniel Kessler</h4><div class="role">Physiotherapist</div>
      <p class="creds">B Pod M Physio</p>
      <svg class="more-icon" width="18" height="18" viewBox="0 0 18 18"><circle cx="9" cy="9" r="9" fill="var(--sage)"/><path d="M9 5v8M5 9h8" stroke="#fff" stroke-width="2"/></svg>
    </div>
  </div>
</section>

<section class="blog">
  <h2 class="section-title">Blog Posts</h2>
  <span class="title-rule"></span>
  <div class="container post-grid">
    <article class="post">
      <div class="post-image" role="img" aria-label="Decorated cake on a plate" style="background:linear-gradient(135deg,#c9a89a,#8e5a4e)"></div>
      <h3>The 2017 OP/OPR Kitchen Cup competition is heating up!</h3>
      <div class="date">Jan 31, 2018</div>
      <p>The stakes are high and the Kitchen Cup competition is taken very seriously here at Oakmere Physiotherapy/Pilates and Rehab.</p>
      <a class="read-more">Read More</a>
    </article>
    <article class="post">
      <div class="post-image" role="img" aria-label="Person holding a sore shoulder" style="background:linear-gradient(135deg,#d8d8da,#9c9ba3)"></div>
      <h3>Wanted: volunteers for shoulder rehabilitation study</h3>
      <div class="date">Jan 31, 2018</div>
      <p>The stakes are high and the Kitchen Cup competition is taken very seriously here at Oakmere Physiotherapy/Pilates and Rehab.</p>
      <a class="read-more">Read More</a>
    </article>
    <article class="post">
      <div class="post-image" role="img" aria-label="Exercise class in a gym with balls" style="background:linear-gradient(135deg,#7e8fa0,#3f5060)"></div>
      <h3>Moving well with osteoarthritis (MWOA)</h3>
      <div class="date">Jan 31, 2018</div>
      <p>The stakes are high and the Kitchen Cup competition is taken very seriously here at Oakmere Physiotherapy/Pilates and Rehab.</p>
      <a class="read-more">Read More</a>
    </article>
  </div>
  <div class="blog-action"><a class="btn btn-sage">Read All Posts</a></div>
</section>

<section class="locations">
  <h2 class="section-title">Our Locations</h2>
  <div class="container location-grid">
    <div class="location">
      <h5>Bayward Vale Physiotherapy</h5>
      <p>48-50 Harlow Parade,<br>Oakmere VIC 3071</p>
      <div class="contact-line"><svg width="12" height="12" viewBox="0 0 12 12"><path d="M2 1h3l1 3-2 1a7 7 0 0 0 3 3l1-2 3 1v3c-6 0-9-3-9-9z" fill="#fff"/></svg>03 9555 0142</div>
      <div class="contact-line"><svg width="12" height="10" viewBox="0 0 12 10"><rect x=".5" y=".5" width="11" height="9" fill="none" stroke="#fff"/><path d="M.5.5 6 5l5.5-4.5" fill="none" stroke="#fff"/></svg>admin@oakmerepilatesandrehab.com.au</div>
      <div class="contact-line"><svg width="10" height="13" viewBox="0 0 10 13"><path d="M5 0a5 5 0 0 1 5 5c0 3-5 8-5 8S0 8 0 5a5 5 0 0 1 5-5z" fill="#fff"/><circle cx="5" cy="5" r="2" fill="var(--dark)"/></svg>Map Direction</div>
    </div>
    <div class="location">
      <h5>Oakmere Pilates &amp; Rehab</h5>
      <p>48-50 Harlow Parade,<br>Oakmere VIC 3071</p>
      <div class="contact-line"><svg width="12" height="12" viewBox="0 0 12 12"><path d="M2 1h3l1 3-2 1a7 7 0 0 0 3 3l1-2 3 1v3c-6 0-9-3-9-9z" fill="#fff"/></svg>03 9555 0142</div>
      <div class="contact-line"><svg width="12" height="10" viewBox="0 0 12 10"><rect x=".5" y=".5" width="11" height="9" fill="none" stroke="#fff"/><path d="M.5.5 6 5l5.5-4.5" fill="none" stroke="#fff"/></svg>admin@oakmerepilatesandrehab.com.au</div>
      <div class="contact-line"><svg width="10" height="13" viewBox="0 0 10 13"><path d="M5 0a5 5 0 0 1 5 5c0 3-5 8-5 8S0 8 0 5a5 5 0 0 1 5-5z" fill="#fff"/><circle cx="5" cy="5" r="2" fill="var(--dark)"/></svg>Map Direction</div>
    </div>
    <div class="location">
      <h5>Oakmere Physiotherapy</h5>
      <p>62 Harlow Parade<br>Oakmere VIC 3071</p>
      <div class="contact-line"><svg width="12" height="12" viewBox="0 0 12 12"><path d="M2 1h3l1 3-2 1a7 7 0 0 0 3 3l1-2 3 1v3c-6 0-9-3-9-9z" fill="#fff"/></svg>03 9555 0187</div>
      <div class="contact-line"><svg width="12" height="10" viewBox="0 0 12 10"><rect x=".5" y=".5" width="11" height="9" fill="none" stroke="#fff"/><path d="M.5.5 6 5l5.5-4.5" fill="none" stroke="#fff"/></svg>admin@oakmerephysiotherapy.com.au</div>
      <div class="contact-line"><svg width="10" height="13" viewBox="0 0 10 13"><path d="M5 0a5 5 0 0 1 5 5c0 3-5 8-5 8S0 8 0 5a5 5 0 0 1 5-5z" fill="#fff"/><circle cx="5" cy="5" r="2" fill="var(--dark)"/></svg>Map Direction</div>
    </div>
  </div>
</section>

<footer class="site-footer">
  <nav class="footer-nav">
    <a>Home</a><a>About</a><a>Service</a><a>Conditions</a><a>Health Tips</a><a>Blog</a><a>Careers</a><a>Contact</a>
  </nav>
  <p class="copyright">Copyright © 2018 Company Name All Right Reserved</p>
  <div class="social"><span></span><span></span></div>
</footer>

</body>
</html>
```